Building company buisness cards

We are looking for a sharp modern new look for our business cards.We are a New Zealand based company that specialises in house and land packages.We have attached a photo of the current logo and would like to see if it can be improved somehow if needed.We are open to any colours but we have chosen Black and White at this stage. Feel free to change the font and make the logo smarter looking.Play with the colours and see what looks best.We want a card that looks so good know one will want to throw it away!

Target Market(s)

Building profesonals, home buyers

Industry/Entity Type

Building

Contact Information for Business Card

Garrick Tenwood
0275390628
garrickt@hartvale.co.nz

Font styles to use
Serif
Sans Serif

Colors

Designer to choose colors to be used in the design.

Requirements
Must have
• Just the logo on one side and details on the other
• Clean simple looking card
Nice to have
• Round corners and detail like raised or spot UV
• Something that stands out
Should not have
• To title needed, Director etc

```html
<!DOCTYPE html>
<html lang="en">
<head>
<meta charset="utf-8">
<title>Hartvale — Business Cards</title>
<link rel="stylesheet" href="https://fonts.googleapis.com/css2?family=Libre+Baskerville:wght@400;700&family=Arimo:wght@400&display=swap">
<style>
  :root {
    --stage: #1f2022;
    --card-dark: #35383b;
    --card-dark-deboss: #2a2c2f;
    --card-light: #ffffff;
    --ink: #111111;
    --ink-faint: #ececec;
    --serif: "Libre Baskerville", "Times New Roman", serif;
    --sans: "Arimo", Arial, sans-serif;
  }
  * { margin: 0; padding: 0; box-sizing: border-box; }
  html, body { width: 1200px; height: 800px; overflow: hidden; }
  body {
    background: var(--stage);
    display: flex;
    align-items: center;
    justify-content: center;
    gap: 40px;
  }
  .card {
    position: relative;
    width: 540px;
    height: 310px;
    border-radius: 22px;
    overflow: hidden;
  }

  /* Front: brand side */
  .card--front { background: var(--card-dark); }
  .front-brand {
    position: absolute;
    inset: 0;
    display: flex;
    align-items: center;
    justify-content: center;
    gap: 18px;
  }
  .front-brand__name {
    font-family: var(--serif);
    font-weight: 700;
    font-size: 60px;
    letter-spacing: -1px;
    color: var(--card-dark-deboss);
  }
  .front-brand__dot {
    width: 58px;
    height: 58px;
    border: 3px solid var(--card-dark-deboss);
    border-radius: 50%;
  }

  /* Back: details side */
  .card--back { background: var(--card-light); color: var(--ink); }
  .back-watermark {
    position: absolute;
    right: -70px;
    top: -40px;
    width: 300px;
    height: 300px;
    border: 14px solid var(--ink-faint);
    border-radius: 50%;
  }
  .back-brand {
    position: absolute;
    left: 46px;
    top: 150px;
    display: flex;
    flex-direction: column;
    align-items: center;
    gap: 10px;
  }
  .back-brand__dot {
    width: 70px;
    height: 70px;
    border: 3px solid var(--ink);
    border-radius: 50%;
  }
  .back-brand__name {
    font-family: var(--serif);
    font-weight: 700;
    font-size: 17px;
    color: var(--ink);
  }
  .back-divider {
    position: absolute;
    left: 178px;
    top: 132px;
    width: 1.5px;
    height: 130px;
    background: var(--ink);
  }
  .contact {
    position: absolute;
    left: 208px;
    top: 120px;
    z-index: 1;
  }
  .contact__name {
    font-family: var(--serif);
    font-weight: 700;
    font-size: 17px;
    padding-bottom: 8px;
    border-bottom: 1.5px solid var(--ink);
    width: 230px;
    margin-bottom: 16px;
  }
  .contact__line {
    display: flex;
    align-items: center;
    gap: 8px;
    font-family: var(--sans);
    font-size: 14px;
    margin-bottom: 8px;
  }
  .contact__icon { width: 16px; height: 16px; flex: none; }
</style>
</head>
<body>
  <section class="card card--front" aria-label="Card front">
    <div class="front-brand">
      <span class="front-brand__name">Hartvale</span>
      <span class="front-brand__dot" aria-hidden="true"></span>
    </div>
  </section>

  <section class="card card--back" aria-label="Card back">
    <div class="back-watermark" aria-hidden="true"></div>
    <div class="back-brand">
      <span class="back-brand__dot" aria-hidden="true"></span>
      <span class="back-brand__name">Hartvale</span>
    </div>
    <div class="back-divider" aria-hidden="true"></div>
    <div class="contact">
      <p class="contact__name">Garrick Tenwood</p>
      <p class="contact__line">
        <svg class="contact__icon" viewBox="0 0 16 16" aria-hidden="true">
          <circle cx="8" cy="8" r="7" fill="none" stroke="#111" stroke-width="1.3"/>
          <rect x="5.5" y="3.8" width="5" height="8.4" rx="1" fill="none" stroke="#111" stroke-width="1.2"/>
        </svg>
        0275390628
      </p>
      <p class="contact__line">
        <svg class="contact__icon" viewBox="0 0 16 16" aria-hidden="true">
          <circle cx="8" cy="8" r="7.5" fill="#111"/>
          <rect x="4" y="5.2" width="8" height="5.6" fill="none" stroke="#fff" stroke-width="1.1"/>
          <path d="M4 5.2 L8 8.6 L12 5.2" fill="none" stroke="#fff" stroke-width="1.1"/>
        </svg>
        garrickt@hartvale.co.nz
      </p>
    </div>
  </section>
</body>
</html>
```